Corvane Spectrix Holdings - Business Cards

I would like a design developed using the logo (number 60387519) previously developed and attached. The information needs to include everything shown on the attached email title block, arranged to suit a business format. I would like a white background, with no other graphics added.
I need an editable version (e.g. MSWord) so I can change the name shown on the business card for others.

Target Market(s)

Mining & Heavy Manufacturing industries

Industry/Entity Type

Mining

Contact Information for Business Card

Refer to attached email title block in MSWord format for the details to be included.

Colors

Designer to choose colors to be used in the design.

Requirements
Must have
• White background, and fonts and text colour to match the unique font in the logo.
Nice to have
• the website address to be shown along the bottom of the card, as it is quite long.
Should not have
• Dark background, or unnecessary graphics

```html
<!DOCTYPE html>
<html lang="en">
<head>
<meta charset="utf-8">
<title>Corvane Spectrix Holdings – Business Card</title>
<link rel="stylesheet" href="https://fonts.googleapis.com/css2?family=Arimo:wght@700&family=Questrial&family=Carlito&display=swap">
<style>
  :root {
    --card-bg: #ffffff;
    --ink: #000000;
    --ink-soft: #595959;
    --link-blue: #2f5fb3;
    --brand-blue: #1670c0;
    --halo: #e8edf7;
    --rule: #000000;
  }
  html, body {
    margin: 0;
    padding: 0;
    width: 1200px;
    height: 686px;
    overflow: hidden;
    background: var(--card-bg);
  }
  .card {
    position: relative;
    width: 1200px;
    height: 686px;
    overflow: hidden;
    background: var(--card-bg);
    font-family: "Questrial", "Century Gothic", sans-serif;
    color: var(--ink);
  }
  .card__halo {
    position: absolute;
    left: 390px;
    top: 95px;
    width: 540px;
    height: 540px;
    border-radius: 50%;
    background: var(--halo);
  }
  .person {
    position: absolute;
    left: 162px;
    top: 108px;
    margin: 0;
  }
  .person__name {
    margin: 0;
    font-family: "Arimo", Arial, sans-serif;
    font-weight: 700;
    font-size: 43px;
    line-height: 48px;
  }
  .person__role {
    margin: 0;
    font-size: 44px;
    line-height: 46px;
  }
  .contact {
    position: absolute;
    left: 162px;
    top: 290px;
    font-size: 31px;
    line-height: 41px;
  }
  .contact__email {
    display: block;
    margin-left: 7px;
    color: var(--link-blue);
    text-decoration: underline;
    text-decoration-thickness: 1px;
  }
  .contact__phone { display: block; margin-left: 8px; }
  .contact__chat { display: block; }
  .rule {
    position: absolute;
    left: 0;
    width: 1200px;
    height: 4px;
    background: var(--rule);
  }
  .rule--top { top: 454px; }
  .rule--bottom { top: 648px; }
  .brand {
    position: absolute;
    left: 95px;
    top: 520px;
    display: flex;
    align-items: center;
    gap: 16px;
  }
  .brand__dot {
    width: 56px;
    height: 56px;
    border-radius: 50%;
    background: var(--brand-blue);
  }
  .brand__name {
    font-size: 27px;
    color: var(--brand-blue);
    white-space: nowrap;
  }
  .office {
    position: absolute;
    left: 587px;
    top: 492px;
    color: var(--ink-soft);
    font-size: 28px;
    line-height: 34px;
  }
  .office p { margin: 0; }
  .office__web {
    position: absolute;
    left: 587px;
    top: 608px;
    font-family: "Carlito", Calibri, sans-serif;
    font-size: 25px;
    color: var(--link-blue);
    text-decoration: underline;
  }
</style>
</head>
<body>
  <div class="card">
    <div class="card__halo" aria-hidden="true"></div>

    <div class="person">
      <h1 class="person__name">Matteo (Teo) Varsano</h1>
      <p class="person__role">Director</p>
    </div>

    <div class="contact">
      <a class="contact__email" href="mailto:matteo.varsano@corvanespectrix.com.au">matteo.varsano@corvanespectrix.com.au</a>
      <span class="contact__phone">+61 400 372 918</span>
      <span class="contact__chat">mtk.matteo.varsano</span>
    </div>

    <div class="rule rule--top"></div>

    <div class="brand">
      <div class="brand__dot" aria-hidden="true"></div>
      <span class="brand__name">Corvane Spectrix Holdings</span>
    </div>

    <div class="office">
      <p>PO BOX 415, Carrington</p>
      <p>NSW 2294, AUSTRALIA</p>
      <p>ABN 48 302 775 193</p>
    </div>
    <a class="office__web" href="#">www.corvanespectrix.com.au</a>

    <div class="rule rule--bottom"></div>
  </div>
</body>
</html>
```